Need Business Card for our Real Estate Business with Sales Executive's Picture

PANTONE 484 C ( RED)

PANTONE 2766 C ( BLUE

Industry/Entity Type

Real Estate

Contact Information for Business Card

Name, Mobile, email, & picture of Person
Agency Phone, address, Web address

Requirements
Must have
• Our Logo Colours, Agent Picture,

```html
<!DOCTYPE html>
<html lang="en">
<head>
<meta charset="utf-8">
<title>Dunmore Realty – Business Card</title>
<link rel="stylesheet" href="https://fonts.googleapis.com/css2?family=Cinzel:wght@600&family=Josefin+Sans:wght@400&display=swap">
<style>
  :root {
    --navy: #141b4d;
    --navy-mid: #1f2a6b;
    --navy-light: #2c3a86;
    --red: #9a3324;
    --paper: #ffffff;
    --paper-shade: #eef0f4;
    --ink: #1d2560;
    --stage: #1b1b1d;
  }
  * { box-sizing: border-box; margin: 0; padding: 0; }
  html, body { width: 1200px; height: 864px; overflow: hidden; }
  body {
    background: var(--stage);
    display: flex;
    align-items: center;
    justify-content: center;
    gap: 40px;
  }
  .card {
    position: relative;
    width: 540px;
    height: 309px;
    overflow: hidden;
  }

  /* Front */
  .card-front {
    background: linear-gradient(180deg, var(--paper) 0%, var(--paper) 55%, var(--paper-shade) 100%);
  }
  .front-brand {
    position: absolute;
    top: 58px;
    left: 0;
    width: 100%;
    display: flex;
    align-items: center;
    justify-content: center;
    gap: 8px;
    font-family: "Cinzel", serif;
    font-weight: 600;
    font-size: 22px;
    letter-spacing: 3px;
    color: var(--navy);
  }
  .brand-square {
    width: 8px;
    height: 8px;
    background: var(--red);
  }
  .name-band {
    position: absolute;
    top: 112px;
    left: 0;
    width: 100%;
    height: 34px;
    background: var(--navy);
  }
  .agent-name {
    position: absolute;
    top: 120px;
    left: 0;
    width: 330px;
    text-align: center;
    font-family: "Cinzel", serif;
    font-weight: 600;
    font-size: 17px;
    letter-spacing: 1.5px;
    color: var(--paper);
  }
  .agent-photo {
    position: absolute;
    top: 80px;
    left: 402px;
    width: 100px;
    height: 100px;
    border-radius: 50%;
    border: 3px solid var(--paper);
    box-shadow: 0 0 0 1.5px var(--navy);
    background: radial-gradient(circle at 50% 35%, #c9b8a6 0%, #7d8aa8 45%, var(--navy-light) 100%);
  }
  .address {
    position: absolute;
    top: 218px;
    left: 34px;
    font-family: "Josefin Sans", sans-serif;
    font-size: 13.5px;
    line-height: 17px;
    color: var(--ink);
    text-align: right;
    width: 200px;
  }
  .contact-list {
    position: absolute;
    top: 190px;
    left: 300px;
    list-style: none;
    font-family: "Josefin Sans", sans-serif;
    font-size: 13px;
    color: var(--ink);
  }
  .contact-list li {
    display: flex;
    align-items: center;
    gap: 9px;
    height: 19px;
  }
  .contact-icon {
    width: 11px;
    height: 11px;
    flex: none;
  }

  /* Back */
  .card-back {
    background: linear-gradient(160deg, var(--navy-light) 0%, var(--navy-mid) 45%, var(--navy) 100%);
    display: flex;
    align-items: center;
    justify-content: center;
    gap: 10px;
  }
  .back-brand {
    font-family: "Cinzel", serif;
    font-weight: 600;
    font-size: 30px;
    letter-spacing: 4px;
    color: var(--paper);
  }
  .card-back .brand-square { width: 10px; height: 10px; }
</style>
</head>
<body>

<section class="card card-front">
  <div class="front-brand"><span class="brand-square"></span>Dunmore Realty</div>
  <div class="name-band"></div>
  <h1 class="agent-name">Leon Marsh</h1>
  <div class="agent-photo" role="img" aria-label="Portrait of the sales executive"></div>

  <p class="address">820 Maple Avenue Suite 310<br>Oak Ridge, Il 60421</p>

  <ul class="contact-list">
    <li>
      <svg class="contact-icon" viewBox="0 0 12 12"><path fill="#9a3324" d="M2.5 1 4.3 1 5 3.6 3.9 4.5Q4.8 6.8 7.3 8L8.3 7 11 7.7 11 9.5Q10.6 11 9 11 1 10 1 2.6 1 1 2.5 1Z"/></svg>
      <span>(09) 412 7300</span>
    </li>
    <li>
      <svg class="contact-icon" viewBox="0 0 12 12"><rect x="3" y="0.8" width="6" height="10.4" rx="1" fill="none" stroke="#9a3324" stroke-width="1.2"/><circle cx="6" cy="9.3" r="0.7" fill="#9a3324"/></svg>
      <span>027 516 4410</span>
    </li>
    <li>
      <svg class="contact-icon" viewBox="0 0 12 12"><rect x="0.8" y="2.2" width="10.4" height="7.6" fill="#9a3324"/><path d="M1 2.5 6 6.6 11 2.5" fill="none" stroke="#fff" stroke-width="1"/></svg>
      <span>leon@dunmorerealty.com</span>
    </li>
    <li>
      <svg class="contact-icon" viewBox="0 0 12 12"><g fill="none" stroke="#9a3324" stroke-width="1"><circle cx="6" cy="6" r="5"/><ellipse cx="6" cy="6" rx="2.2" ry="5"/><path d="M1 6h10M2 3.3h8M2 8.7h8"/></g></svg>
      <span>www.dunmorerealty.com</span>
    </li>
  </ul>
</section>

<section class="card card-back">
  <span class="brand-square"></span>
  <span class="back-brand">Dunmore Realty</span>
</section>

</body>
</html>
```